Aunt Roula's Bakery

I am about to create a luxury boutique that specializes in cake baking and cupcake
and ready for parties and special events and order delivery
the logo has already made

Boutique

Email:auntroulasbakery@mailbox-example.net
Instagram: aunt_roula_bakery
Twitter: xxxxxxx
WhatsApp: xxxxxxx

Requirements
Must have
• luxury design

```html
<!DOCTYPE html>
<html lang="en">
<head>
<meta charset="utf-8">
<title>Aunt Roula's Bakery — Business Card</title>
<link rel="stylesheet" href="https://fonts.googleapis.com/css2?family=Montserrat:wght@400;600;700&display=swap">
<style>
  :root {
    --stage: #e9e5e1;
    --card-black: #0d0d0d;
    --card-sheen: #2a2a2a;
    --rose: #c99bb0;
    --rose-deep: #b07f97;
    --ink-light: #f2f2f2;
    --ink-muted: #b9b9b9;
    --ornament: #2b2b2b;
  }
  * { box-sizing: border-box; margin: 0; padding: 0; }
  html, body { width: 1200px; height: 1022px; overflow: hidden; }
  body {
    background: var(--stage);
    display: flex; align-items: center; justify-content: center;
    font-family: "Montserrat", Arial, sans-serif;
  }
  .business-card {
    position: relative;
    width: 1000px; height: 572px;
    background: linear-gradient(150deg, var(--card-sheen) 0%, var(--card-black) 45%, var(--card-black) 100%);
    border-radius: 6px;
    box-shadow: 0 18px 40px rgba(0,0,0,.25);
    overflow: hidden;
    color: var(--ink-light);
  }
  .corner-ornament {
    position: absolute; top: 0; right: 0;
    width: 420px; height: 260px;
    background: radial-gradient(ellipse at top right, var(--ornament) 0%, rgba(43,43,43,0) 70%);
  }
  .logo-ornament {
    position: absolute; left: 70px; top: 150px;
    width: 300px; height: 200px;
    background: radial-gradient(ellipse at center, #1f1f1f 0%, rgba(31,31,31,0) 72%);
  }
  .brand {
    position: absolute; left: 90px; top: 215px;
    display: flex; align-items: center; gap: 16px;
  }
  .brand-dot {
    width: 54px; height: 54px; border-radius: 50%;
    background: var(--rose);
  }
  .brand-name {
    font-weight: 600; font-size: 26px; letter-spacing: 2px;
    text-transform: uppercase; color: var(--ink-muted);
  }
  .owner {
    position: absolute; right: 70px; top: 70px; text-align: right;
  }
  .owner-name {
    font-weight: 700; font-size: 38px; letter-spacing: 1px;
    text-transform: uppercase; color: var(--ink-light);
  }
  .owner-role {
    display: flex; align-items: center; justify-content: flex-end; gap: 4px;
    margin-top: 4px;
    font-size: 17px; letter-spacing: 1px; color: var(--rose);
    text-transform: uppercase;
  }
  .owner-role::before {
    content: ""; width: 120px; height: 1px; background: var(--ink-muted);
  }
  .divider {
    position: absolute; left: 420px; right: 70px; top: 195px;
    height: 2px; background: var(--ink-muted);
  }
  .contacts {
    position: absolute; left: 420px; top: 300px;
    list-style: none;
    font-size: 22px; line-height: 38px; color: var(--ink-light);
  }
  .contacts li { display: flex; align-items: center; gap: 14px; }
  .contact-mark {
    width: 16px; height: 16px; border-radius: 3px;
    border: 2px solid var(--ink-muted);
  }
  .contact-mark.round { border-radius: 50%; }
  .accent-band {
    position: absolute; left: 0; right: 0; bottom: 0;
    height: 64px;
    background: linear-gradient(180deg, var(--rose) 0%, var(--rose-deep) 100%);
  }
</style>
</head>
<body>
  <article class="business-card">
    <div class="corner-ornament" role="img" aria-label="Faint swirling scroll ornament"></div>
    <div class="logo-ornament" role="img" aria-label="Decorative scrollwork framing the bakery name"></div>

    <div class="brand">
      <span class="brand-dot"></span>
      <span class="brand-name">Aunt Roula's Bakery</span>
    </div>

    <div class="owner">
      <p class="owner-name">Aunt Roula</p>
      <p class="owner-role">Owner</p>
    </div>

    <div class="divider"></div>

    <ul class="contacts">
      <li><span class="contact-mark round"></span>xxxxxxx</li>
      <li><span class="contact-mark round"></span>xxxxxxx</li>
      <li><span class="contact-mark"></span>aunt_roula_bakery</li>
      <li><span class="contact-mark"></span>auntroulasbakery@mailbox-example.net</li>
    </ul>

    <div class="accent-band"></div>
  </article>
</body>
</html>
```